National Networking/Telecommunications Company needs a new packaging (bag) design

We are currently going through a re-branding stage and need to create new packaging for all of our material.

We need a complete redesign of our current packaging (which is in various sizes). I have attached the current die-lines/knife for one of our bags.

- VORTELL logos to be changed to our BRANQOR logo (attached)
- BRANQOR logo to be modified, so it simply says the word BRANQOR with the tick image on the end. Please remove all other writing (PROVEN SYSTEMS & WIDE RANGE, LASTING QUALITY) removed from the logo. Once this has been removed, please resize the word BRANQOR, so it fits nicely beside the tick logo.
- Please remove all references to VORTELL websites, and replace with www.branqor.com.au
- Remove "Network, Computer and Audio Video Connectivity Solutions"
- Keeping the logos that say "Lifetime Warranty" and "100% Tested and Certified", open to different ideas on how to portray them on the bag.
- Our main company colours are red, blue & silver. We're open to all designs. Packaging needs to STAND OUT, without looking cheap. Needs to still look professional and classy.
- The inside backing of the bag is to be white in colour.

I have attached our new cable box design, if that helps with keeping the colours the same.

Target Market(s)

Electrical wholesalers (who stock this product), IT/System Integrators, Installers

Industry/Entity Type

Telecommunications

Font styles to use
Sans Serif

Requirements
Must have
• Our company colours (blue, red, white/silver)
Nice to have
• Overall design needs to be simplistic, yet elegant and professional.
Should not have
• Should not have the word VORTELL anywhere

```html
<!DOCTYPE html>
<html lang="en">
<head>
<meta charset="utf-8">
<title>BRANQOR Hang Bag Packaging</title>
<link rel="stylesheet" href="https://fonts.googleapis.com/css2?family=Montserrat:wght@600;700&display=swap">
<style>
  :root {
    --backdrop: #d4d4d4;
    --navy: #10143a;
    --navy-line: #2a3060;
    --window: #ffffff;
    --silver: #c9cacd;
    --red: #e3202a;
    --badge: #e9e9ec;
    --badge-ring: #9a9ca4;
    --url: #ffffff;
  }
  html, body {
    margin: 0;
    padding: 0;
    width: 1200px;
    height: 2429px;
    overflow: hidden;
    background: var(--backdrop);
  }
  .canvas {
    position: relative;
    width: 1200px;
    height: 2429px;
  }
  .hang-bag {
    position: absolute;
    left: 250px;
    top: 654px;
    width: 700px;
    height: 1120px;
    display: block;
  }
  .bag-body { fill: var(--navy); }
  .seal-line, .header-line { stroke: var(--navy-line); stroke-width: 1.5; }
  .hang-hole { fill: var(--backdrop); }
  .product-window { fill: var(--window); }
  .brand-name {
    font-family: "Montserrat", sans-serif;
    font-weight: 600;
    font-size: 84px;
    letter-spacing: 6px;
    fill: var(--silver);
  }
  .brand-dot { fill: var(--red); }
  .badge-disc { fill: var(--badge); stroke: var(--badge-ring); stroke-width: 4; }
  .badge-ring { fill: none; stroke: var(--navy); stroke-width: 3; }
  .web-address {
    font-family: "Montserrat", sans-serif;
    font-weight: 700;
    font-size: 19px;
    letter-spacing: 1.5px;
    fill: var(--url);
  }
</style>
</head>
<body>
<main class="canvas">
  <svg class="hang-bag" viewBox="0 0 700 1120" xmlns="http://www.w3.org/2000/svg">
    <rect class="bag-body" x="0" y="0" width="700" height="1120"/>

    <line class="seal-line" x1="0" y1="70" x2="700" y2="70"/>
    <line class="header-line" x1="0" y1="210" x2="700" y2="210"/>

    <path class="hang-hole" d="M300 360 Z M292 182 H336 A14 14 0 0 1 364 182 H408 A10 10 0 0 1 408 202 H292 A10 10 0 0 1 292 182 Z" transform="translate(0,0)"/>

    <g class="brand-lockup">
      <text class="brand-name" x="330" y="402" text-anchor="middle">BRANQOR</text>
      <circle class="brand-dot" cx="644" cy="373" r="20"/>
    </g>

    <polygon class="product-window" points="0,510 700,510 700,775 529,938 147,938 0,775"/>

    <g class="quality-badges">
      <circle class="badge-disc" cx="287" cy="1003" r="60" role="img" aria-label="Lifetime warranty badge"/>
      <circle class="badge-ring" cx="287" cy="1003" r="44"/>
      <circle class="badge-disc" cx="434" cy="1003" r="60" role="img" aria-label="100% tested and certified badge"/>
      <circle class="badge-ring" cx="434" cy="1003" r="44"/>
    </g>

    <text class="web-address" x="350" y="1100" text-anchor="middle">www.branqor.com.au</text>
  </svg>
</main>
</body>
</html>
```